Dynamic Business Card for Sports Supplements Company

Hi! I'm looking for an awesome business card to match my existing sports supplement company. I have uploaded my current company logo and screenshot of the front page of my website.

I would like to have something dynamic and interesting and utilize the colors in the website - the reds and purples

The business card should be double sided and focus on a unique eye-catching design on the back and include all the relevant company info.

Most importantly, it should say somewhere: "Sign up on our website for a coupon code."

Target Market(s)

Mostly for women gym goers but it shouldn't be too feminine. It should be in keeping with the website design. It should flow and clearly be connected to it

Industry/Entity Type

Business

Contact Information for Business Card

Lorraine K. Vestal
CEO
LVestal@Quorvanexco.com
www.quorvanexco.com
555.417.3820
P.O. Box 47315
Larkhaven, Norvale 00000

Sign up on our website for a coupon code

Font styles to use
Serif
Sans Serif
Other font styles liked:
• Novecento font family and "Quorvanex" is in AR Destine font

Requirements
Must have
• One side should be a bold Quorvanex logo design. Even just the symbol itself may be o.k. (see attached file)

```html
<!DOCTYPE html>
<html lang="en">
<head>
<meta charset="utf-8">
<title>Quorvanex Business Card</title>
<link rel="stylesheet" href="https://fonts.googleapis.com/css2?family=Orbitron:wght@700&family=Michroma&family=Open+Sans:wght@400;600&display=swap">
<style>
  :root {
    --stage: #c8c8c8;
    --paper: #ffffff;
    --ink: #1b1b1d;
    --brand-red: #e21f26;
    --night: #111215;
    --night-glow: #3a3b40;
    --white: #ffffff;
  }
  * { margin: 0; padding: 0; box-sizing: border-box; }
  html, body {
    width: 1200px; height: 900px; overflow: hidden;
    background: var(--stage);
  }
  .stage { position: relative; width: 1200px; height: 900px; }

  .card {
    position: absolute;
    top: 271px;
    width: 457px; height: 282px;
    border-radius: 14px;
    overflow: hidden;
    box-shadow: 2px 3px 5px rgba(0,0,0,0.35);
  }

  /* Front */
  .card--front { left: 137px; background: var(--paper); }
  .front__band {
    position: absolute; left: 346px; top: 0; width: 111px; height: 100%;
    background: radial-gradient(ellipse at 30% 30%, var(--night-glow) 0%, var(--night) 70%);
  }
  .brand-name {
    font-family: "Orbitron", sans-serif;
    font-weight: 700;
    color: var(--brand-red);
    text-transform: uppercase;
    line-height: 1;
  }
  .brand-tagline {
    font-family: "Michroma", sans-serif;
    text-transform: uppercase;
    line-height: 1;
    white-space: nowrap;
  }
  .front__brand { position: absolute; left: 28px; top: 27px; font-size: 29px; letter-spacing: 0.5px; }
  .front__tagline { position: absolute; left: 29px; top: 55px; font-size: 8.5px; letter-spacing: 1.9px; color: var(--ink); }

  .person__name {
    position: absolute; left: 27px; top: 101px;
    font-family: "Michroma", sans-serif; font-size: 13.5px; letter-spacing: 0.6px;
    color: var(--brand-red); font-weight: 400; white-space: nowrap;
  }
  .person__title {
    position: absolute; left: 27px; top: 119px;
    font-family: "Open Sans", sans-serif; font-size: 13.5px; color: var(--ink);
  }
  .contact-list {
    position: absolute; left: 27px; top: 146px; list-style: none;
    font-family: "Open Sans", sans-serif; font-size: 13px; color: var(--ink);
  }
  .contact-list li { display: flex; align-items: center; height: 21px; }
  .contact-list svg { width: 11px; height: 11px; margin-right: 8px; fill: var(--brand-red); }
  .address {
    position: absolute; left: 27px; top: 218px;
    font-family: "Open Sans", sans-serif; font-size: 13px; line-height: 17px; color: var(--ink);
    font-style: normal;
  }

  /* Back */
  .card--back {
    left: 626px;
    background: radial-gradient(ellipse at 50% 75%, #2e2f34 0%, var(--night) 60%, #08090b 100%);
    text-align: center;
  }
  .back__mark {
    position: absolute; left: 209px; top: 95px; width: 40px; height: 40px;
    background: var(--brand-red);
  }
  .back__brand {
    position: absolute; left: 0; right: 0; top: 168px;
    font-size: 25px; color: var(--white); letter-spacing: 0.5px;
  }
  .back__tagline {
    position: absolute; left: 0; right: 0; top: 194px;
    font-size: 7.5px; letter-spacing: 1.7px; color: var(--white);
  }
  .back__offer {
    position: absolute; left: 0; right: 0; top: 229px;
    font-family: "Open Sans", sans-serif; font-size: 12.5px; color: var(--white);
  }
  .back__offer em { font-style: normal; color: var(--brand-red); }
</style>
</head>
<body>
<main class="stage">
  <section class="card card--front" aria-label="Business card front">
    <div class="front__band"></div>
    <h1 class="brand-name front__brand">Quorvanex</h1>
    <p class="brand-tagline front__tagline">Your Training Companion</p>
    <h2 class="person__name">LORRAINE K. VESTAL</h2>
    <p class="person__title">CEO</p>
    <ul class="contact-list">
      <li>
        <svg viewBox="0 0 12 12" aria-hidden="true"><path d="M1 4c0-2 2-3 5-3s5 1 5 3v1H8.5V4h-5v1H1z M3 6h6l1.5 4.5h-9z"/></svg>
        555.417.3820
      </li>
      <li>
        <svg viewBox="0 0 12 12" aria-hidden="true"><path d="M0 2h12v8H0z" /><path d="M0.6 2.6L6 6.8l5.4-4.2" stroke="#fff" stroke-width="1.1" fill="none"/></svg>
        LVestal@Quorvanexco.com
      </li>
      <li>
        <svg viewBox="0 0 12 12" aria-hidden="true"><circle cx="6" cy="6" r="5.5"/><path d="M3 3.5c1.5 0 2 1 3 1.2s.5 1.8-.6 2c-1 .2-.7 1.8-1.6 2.3C3 8 2.4 6 3 3.5z M7.5 7.5c1-.3 1.8.2 2 1-.6.8-1.2 1.2-1.8 1.4-.3-.8-.6-1.6-.2-2.4z" fill="#fff"/></svg>
        www.quorvanexco.com
      </li>
    </ul>
    <address class="address">P.O. Box 47315<br>Larkhaven, Norvale 00000</address>
  </section>

  <section class="card card--back" aria-label="Business card back">
    <div class="back__mark"></div>
    <p class="brand-name back__brand">Quorvanex</p>
    <p class="brand-tagline back__tagline">Your Training Companion</p>
    <p class="back__offer"><em>Sign up</em> on our website for a coupon code</p>
  </section>
</main>
</body>
</html>
```